Australian Trucking Company Requires Professional Looking Stationary

We require a professional looking stationary design that incorporates our newly designed logo.

Our business, called "Brell Haulage Contracting", provides contracting work, transport and logistics to business in Western Australia particularly with links to the mining sector.

We are a small business looking to expand and our new logo and our new stationary will help develop our brand image in our market place.

Target Market(s)

Businesses and Corporation with links to the Mining Sector

Industry/Entity Type

Small Business

Requirements
Must have
• The letterhead must have the following details:
The new logo

Text saying: "Brell Holdings Pty Ltd (ACN 582 316 907) ATF The Brell Discretionary Trust T/AS"
"ABN 71 834 209 553"
Address "P.O Box 817 Wattlegrove WA, 6958"
Phone: 08 9352 7140
Email: brellhaul@mailbox-example.com.au

The text on the letterhead should be editable as the details are likely to change in the near future. Provision should be made for a website address all though one isn't available at the moment.

The styling, layout and font text is entirely up to the designer.

```html
<!DOCTYPE html>
<html lang="en">
<head>
<meta charset="utf-8">
<title>Brell Haulage Contracting – Stationery</title>
<link rel="stylesheet" href="https://fonts.googleapis.com/css2?family=Arimo:wght@400;700&family=Titillium+Web:wght@700&display=swap">
<style>
  :root {
    --backdrop: #ece9e4;
    --card-white: #ffffff;
    --brand-red: #c8161d;
    --deep-red: #7a0a0e;
    --wine: #8e1016;
    --mark-grey: #8a8a8a;
    --truck-tint: #d9a3a5;
    --text-white: #ffffff;
  }
  * { margin: 0; padding: 0; box-sizing: border-box; }
  html, body {
    width: 1200px; height: 428px; overflow: hidden;
    background: var(--backdrop);
    font-family: "Arimo", Arial, sans-serif;
  }
  .stage { position: relative; width: 1200px; height: 428px; }

  /* Letterhead: only its lower edge is in view above the cards */
  .letterhead-edge {
    position: absolute; left: 338px; top: 0;
    width: 796px; height: 6px;
    background: linear-gradient(90deg, var(--wine), var(--brand-red));
    box-shadow: 0 1px 3px rgba(0,0,0,0.25);
  }

  .card {
    position: absolute;
    width: 480px; height: 275px;
    border-radius: 18px;
    overflow: hidden;
    box-shadow: 0 2px 6px rgba(0,0,0,0.18);
  }

  /* Front */
  .card-front { left: 12px; top: 72px; background: var(--card-white); }
  .card-front .wave { position: absolute; inset: 0; width: 480px; height: 275px; }

  .brand { position: absolute; left: 16px; top: 22px; display: flex; align-items: flex-start; gap: 16px; }
  .brand-square { width: 88px; height: 68px; background: var(--mark-grey); opacity: 0.75; border-radius: 4px; }
  .brand-name {
    font-family: "Titillium Web", Arial, sans-serif;
    font-weight: 700;
    font-size: 23px;
    line-height: 24px;
    color: var(--brand-red);
    text-transform: uppercase;
    letter-spacing: 0.5px;
    margin-top: 2px;
  }

  .holder { position: absolute; left: 35px; top: 163px; }
  .holder-name { font-size: 17px; font-weight: 700; color: var(--wine); }
  .holder-title { font-size: 14px; color: var(--wine); letter-spacing: 1px; margin-top: 4px; }

  .contact {
    position: absolute; right: 14px; top: 165px;
    list-style: none;
    color: var(--text-white);
    font-size: 12.5px;
  }
  .contact li { display: flex; justify-content: flex-end; align-items: center; gap: 9px; height: 20.5px; }
  .contact svg { width: 11px; height: 11px; fill: var(--text-white); flex: none; }

  /* Back */
  .card-back {
    left: 647px; top: 95px;
    background: linear-gradient(90deg, var(--deep-red) 0%, var(--wine) 40%, var(--brand-red) 100%);
  }
  .truck-art {
    position: absolute; left: 0; top: 0;
    width: 246px; height: 275px;
    background: linear-gradient(180deg, rgba(217,163,165,0.55), rgba(217,163,165,0.75));
    border-radius: 18px 0 0 18px;
  }
  .web-address {
    position: absolute; left: 244px; top: 127px;
    color: var(--text-white);
    font-size: 17px;
    letter-spacing: 1px;
  }
  .web-address strong { font-weight: 700; }
</style>
</head>
<body>
<main class="stage">

  <div class="letterhead-edge" aria-label="Letterhead lower edge"></div>

  <section class="card card-front" aria-label="Business card front">
    <svg class="wave" viewBox="0 0 480 275" aria-hidden="true">
      <defs>
        <linearGradient id="redFill" x1="0" y1="0" x2="1" y2="0">
          <stop offset="0" stop-color="#7a0a0e"/>
          <stop offset="1" stop-color="#9c0f15"/>
        </linearGradient>
        <linearGradient id="silverLine" x1="0" y1="0" x2="1" y2="0">
          <stop offset="0" stop-color="#2a2a2a"/>
          <stop offset="0.3" stop-color="#f2f2f2"/>
          <stop offset="0.6" stop-color="#9a9a9a"/>
          <stop offset="1" stop-color="#1c1c1c"/>
        </linearGradient>
      </defs>
      <path d="M0,232 C140,262 250,190 330,128 C390,88 440,76 480,74 L480,275 L0,275 Z" fill="url(#redFill)"/>
      <path d="M0,246 C150,270 260,205 340,142 C400,98 445,86 480,86" fill="none" stroke="url(#silverLine)" stroke-width="7"/>
      <path d="M0,255 C150,278 270,215 350,152 C405,108 448,96 480,96" fill="none" stroke="#1c1c1c" stroke-width="3"/>
      <path d="M0,224 C140,250 250,182 330,120 C390,82 440,70 480,68" fill="none" stroke="#8e1016" stroke-width="3"/>
    </svg>

    <div class="brand">
      <div class="brand-square" aria-hidden="true"></div>
      <p class="brand-name">Brell<br>Haulage<br>Contracting</p>
    </div>

    <div class="holder">
      <p class="holder-name">Your Name</p>
      <p class="holder-title">Title</p>
    </div>

    <ul class="contact">
      <li>08 9352 7140
        <svg viewBox="0 0 12 12"><path d="M3 1l2 2-1 1.5c.6 1.4 1.6 2.4 3 3L8.5 6.5l2 2L9 10.5C5 10 2 7 1.5 3z"/></svg></li>
      <li>brellhaul@mailbox-example.com.au
        <svg viewBox="0 0 12 12"><path d="M1 3h10v6H1z"/></svg></li>
      <li>www.brellhaul.com.au
        <svg viewBox="0 0 12 12"><circle cx="6" cy="6" r="5" fill="none" stroke="#fff" stroke-width="1.2"/><path d="M1 6h10M6 1v10" stroke="#fff" stroke-width="1"/></svg></li>
      <li>P.O Box 817 Wattlegrove WA, 6958
        <svg viewBox="0 0 12 12"><path d="M6 1l5 5H9.5v5h-2.5V8H5v3H2.5V6H1z"/></svg></li>
    </ul>
  </section>

  <section class="card card-back" aria-label="Business card back">
    <div class="truck-art" role="img" aria-label="Large faint illustration of a truck front"></div>
    <p class="web-address">www.<strong>brellhaul</strong>.com</p>
  </section>

</main>
</body>
</html>
```